Ridgeline Haul Carriers - Website

A clean, not cluttered informative website for our business. We specialize in the transportation of radioactive materials across North America. The site is mostly for information about our company and will not be used to attract business but will be used to attract employee's mainly drivers. Driver's are very hard to find in our area. One of the pages needs to be a job's posting page with an apply now button. Either an application can be filled out there or a resume can be uploaded which ever functionality works better. I would like a website that I can easily edit, ability to change text and photos.

Number of Pages Required

5+ page

Colors

Designer to choose colors to be used in the design.

Requirements
Must have
• Home - About - Services - Jobs - Contact pages
• A way prospective employee's can apply or upload their resume to be emailed to me
• Very clean apperance
Should not have
• I don't want it to be busy

```html
<!DOCTYPE html>
<html lang="en">
<head>
<meta charset="utf-8">
<title>Ridgeline Haul Carriers</title>
<link href="https://fonts.googleapis.com/css2?family=Roboto:wght@300;400;500;700&display=swap" rel="stylesheet">
<style>
:root{
  --red:#d7262e;
  --red-dark:#9e1117;
  --blue:#1f4f9e;
  --blue-dark:#123775;
  --ink:#222428;
  --muted:#6b6e74;
  --line:#d9dbe0;
  --footer:#1c1d20;
  --footer-deep:#141517;
  --white:#ffffff;
}
*{box-sizing:border-box;margin:0;padding:0}
html,body{width:1200px;height:3592px;overflow:hidden}
body{font-family:"Roboto",Arial,sans-serif;color:var(--ink);background:var(--white);position:relative}
.abs{position:absolute}

/* header */
.site-header{position:absolute;left:0;top:0;width:1200px;height:140px;background:var(--white)}
.brand{position:absolute;left:72px;top:28px;font-size:40px;font-weight:700;color:var(--red);letter-spacing:1px;line-height:1}
.brand-sub{position:absolute;left:74px;top:74px;font-size:20px;font-weight:500;color:var(--ink);letter-spacing:9px}
.topbar{position:absolute;right:70px;top:22px;display:flex;align-items:center;gap:22px;font-size:20px;font-weight:500}
.topbar .phone{display:flex;align-items:center;gap:8px}
.search{width:160px;height:32px;border:1px solid var(--line);display:flex;align-items:center;justify-content:space-between;padding:0 10px;font-size:15px;color:var(--muted)}
.nav{position:absolute;right:70px;top:78px;display:flex;gap:52px;font-size:19px;font-weight:500}
.nav a{color:var(--ink);text-decoration:none}
.nav a.active{color:var(--red)}

/* hero */
.hero{position:absolute;left:0;top:140px;width:1200px;height:580px;background:linear-gradient(100deg,#1b1c20 0%,#3a3d44 45%,#6d7078 70%,#2a2c31 100%)}
.hero-photo{position:absolute;left:560px;top:40px;width:600px;height:520px;background:radial-gradient(ellipse at 55% 50%,#b5202a 0%,#7d1218 35%,rgba(40,40,46,0) 70%)}
.hero-title{position:absolute;left:90px;top:210px;color:var(--white);font-size:56px;font-weight:500}
.hero-sub{position:absolute;left:90px;top:290px;color:var(--white);font-size:36px;font-weight:400;line-height:1.35;width:720px}
.dots{position:absolute;left:90px;top:490px;display:flex;gap:10px}
.dots span{width:10px;height:10px;border-radius:50%;background:rgba(255,255,255,.45)}
.dots span.on{background:var(--white)}

/* welcome */
.welcome-frame{position:absolute;left:488px;top:828px;width:632px;height:372px;border:3px solid var(--line);background:var(--white)}
.welcome-photo{position:absolute;left:88px;top:840px;width:520px;height:360px;background:linear-gradient(160deg,#dfe4ea 0%,#aeb7c2 55%,#6f7884 100%);box-shadow:0 6px 18px rgba(0,0,0,.15)}
.play{position:absolute;left:220px;top:160px;width:64px;height:64px;border-radius:50%;background:rgba(255,255,255,.9)}
.welcome-text{position:absolute;left:672px;top:868px;width:420px}
.eyebrow{color:var(--blue);font-size:24px;font-weight:500;letter-spacing:1px}
.h-big{font-size:30px;font-weight:500;margin-top:4px;letter-spacing:.5px}
.body-copy{font-size:15.5px;line-height:1.7;color:var(--muted);margin-top:22px}
.btn-red{display:inline-block;background:var(--red);color:var(--white);font-size:15px;padding:8px 20px;border-radius:18px;margin-top:22px}

/* services */
.services{position:absolute;left:0;top:1320px;width:1200px;height:720px;background:linear-gradient(180deg,var(--blue) 0%,var(--blue-dark) 40%,#f1f3f6 40%,#f1f3f6 100%)}
.services h2{position:absolute;left:0;top:80px;width:1200px;text-align:center;color:var(--white);font-size:46px;font-weight:400}
.card{position:absolute;top:208px;width:320px;height:424px;background:var(--white);box-shadow:0 6px 20px rgba(0,0,0,.15);text-align:center}
.card-photo{height:200px}
.card h3{font-size:24px;font-weight:400;margin-top:28px}
.card p{font-size:15px;line-height:1.6;color:var(--muted);padding:12px 34px 0}
.card .btn-red{margin-top:14px;padding:6px 18px;font-size:14px}
.slider-dash{position:absolute;top:672px;left:528px;display:flex;gap:16px}
.slider-dash span{width:36px;height:4px;background:#9aa3b1}
.slider-dash span.on{background:var(--blue)}

/* job */
.job-box{position:absolute;left:88px;top:2140px;width:1024px;height:400px;background:var(--white);box-shadow:0 6px 24px rgba(0,0,0,.14)}
.job-photo{position:absolute;left:0;top:0;width:432px;height:400px;background:linear-gradient(135deg,#f2c47a 0%,#c9843a 30%,#4d3a2c 70%,#22201f 100%)}
.job-text{position:absolute;left:484px;top:36px;width:500px}
.job-text h2{font-size:46px;font-weight:400;letter-spacing:1px}
.job-text .body-copy{margin-top:18px}
.btn-outline{display:inline-block;border:2px solid var(--blue);color:var(--blue);font-size:15px;padding:6px 20px;border-radius:18px;margin-top:22px}

/* contact */
.contact{position:absolute;left:0;top:2720px;width:1200px;height:460px}
.contact-panel{position:absolute;left:0;top:0;width:660px;height:460px;background:linear-gradient(135deg,var(--red) 0%,var(--red-dark) 100%)}
.contact-panel h2{position:absolute;left:88px;top:46px;color:var(--white);font-size:44px;font-weight:400}
.field{position:absolute;left:88px;width:440px;border-bottom:1px solid rgba(255,255,255,.7);color:var(--white);font-size:19px;padding-bottom:8px}
.submit{position:absolute;left:88px;top:372px;background:var(--white);color:var(--ink);font-size:19px;padding:6px 26px;border-radius:20px}
.map{position:absolute;left:660px;top:0;width:540px;height:460px;background:linear-gradient(160deg,#eef0f2 0%,#d9dde2 100%)}

/* footer */
.site-footer{position:absolute;left:0;top:3180px;width:1200px;height:412px;background:var(--footer);color:#cfd1d5}
.foot-brand{position:absolute;left:88px;top:190px;font-size:32px;font-weight:700;color:var(--white);letter-spacing:1px}
.foot-brand-sub{position:absolute;left:90px;top:228px;font-size:15px;color:var(--white);letter-spacing:6px}
.foot-col{position:absolute;top:44px}
.foot-col h4{font-size:20px;font-weight:500;color:var(--white);margin-bottom:24px}
.foot-col li{list-style:none;font-size:15px;line-height:1.5;margin-bottom:12px;display:flex;gap:12px;align-items:flex-start}
.bullet{width:6px;height:6px;border-radius:50%;background:#cfd1d5;margin-top:8px}
.ring{width:26px;height:26px;border-radius:50%;border:1.5px solid #cfd1d5;flex:none}
.foot-bottom{position:absolute;left:0;bottom:0;width:1200px;height:64px;background:var(--footer-deep);text-align:center;font-size:15px;line-height:64px;color:#a9acb2}
</style>
</head>
<body>

<header class="site-header">
  <div class="brand">RIDGELINE</div>
  <div class="brand-sub">HAUL CARRIERS</div>
  <div class="topbar">
    <div class="phone">
      <svg width="18" height="18" viewBox="0 0 24 24"><path d="M6.6 10.8a15.1 15.1 0 0 0 6.6 6.6l2.2-2.2a1 1 0 0 1 1-.25 11.4 11.4 0 0 0 3.6.57 1 1 0 0 1 1 1V20a1 1 0 0 1-1 1A17 17 0 0 1 3 4a1 1 0 0 1 1-1h3.5a1 1 0 0 1 1 1c0 1.25.2 2.45.57 3.57a1 1 0 0 1-.25 1z" fill="#222428"/></svg>
      1-800-555-0148
    </div>
    <div class="search">Search
      <svg width="14" height="14" viewBox="0 0 24 24"><circle cx="10" cy="10" r="7" stroke="#222428" stroke-width="2.5" fill="none"/><path d="M15 15l6 6" stroke="#222428" stroke-width="2.5"/></svg>
    </div>
  </div>
  <nav class="nav">
    <a class="active">Home</a><a>About Us</a><a>Services</a><a>Jobs</a><a>Contact</a>
  </nav>
</header>

<section class="hero">
  <div class="hero-photo" role="img" aria-label="Red semi truck with white trailer on the highway"></div>
  <h1 class="hero-title">Ridgeline Haul Carriers</h1>
  <p class="hero-sub">Transportation of radioactive materials across North America</p>
  <div class="dots"><span class="on"></span><span></span><span></span></div>
</section>

<div class="welcome-frame"></div>
<div class="welcome-photo" role="img" aria-label="Fleet of white trucks parked at a terminal">
  <div class="play"><svg width="64" height="64" viewBox="0 0 64 64"><path d="M26 20l18 12-18 12z" fill="#222428"/></svg></div>
</div>
<div class="welcome-text">
  <div class="eyebrow">WELCOME TO</div>
  <div class="h-big">RIDGELINE HAUL CARRIERS</div>
  <p class="body-copy">Ridgeline Haul Carriers moves licensed radioactive freight safely across North America. Our drivers are trained, certified and supported by a dispatch team that knows every route. We keep our fleet modern, our schedules fair and our safety record spotless, so every load arrives on time and every driver gets home.</p>
  <span class="btn-red">Read More</span>
</div>

<section class="services">
  <h2>OUR SERVICES</h2>
  <article class="card" style="left:96px">
    <div class="card-photo" role="img" aria-label="White tanker truck on the road" style="background:linear-gradient(160deg,#c9d3df,#5c6a7c)"></div>
    <h3>Neque Porro</h3>
    <p>Certified hauling of sealed radioactive cargo with full regulatory compliance.</p>
    <span class="btn-red">Read More</span>
  </article>
  <article class="card" style="left:440px">
    <div class="card-photo" role="img" aria-label="Blue truck parked at night" style="background:linear-gradient(160deg,#2b4f8c,#0f1f3d)"></div>
    <h3>Dolorem Ipsum</h3>
    <p>Late model tractors and trailers maintained to the highest standard.</p>
    <span class="btn-red">Read More</span>
  </article>
  <article class="card" style="left:784px">
    <div class="card-photo" role="img" aria-label="Mechanic servicing a truck engine" style="background:linear-gradient(160deg,#8fb0d4,#2e4868)"></div>
    <h3>Neque Porro</h3>
    <p>Secure dispatch and live tracking for every shipment we carry.</p>
    <span class="btn-red">Read More</span>
  </article>
  <div class="slider-dash"><span class="on"></span><span></span><span></span></div>
</section>

<section class="job-box">
  <div class="job-photo" role="img" aria-label="Driver's hands on a truck steering wheel at sunset"></div>
  <div class="job-text">
    <h2>AVAILABLE JOB</h2>
    <p class="body-copy">We are hiring experienced Class A drivers for regional and long haul routes. Hazmat endorsement is preferred, and we provide full training for radioactive loads. Enjoy steady miles, competitive pay, benefits from day one and a team that respects your time at home. Send us your application or upload your resume today.</p>
    <span class="btn-outline">Apply Now</span>
  </div>
</section>

<section class="contact">
  <div class="contact-panel">
    <h2>CONTACT US</h2>
    <div class="field" style="top:140px">Name *</div>
    <div class="field" style="top:200px">E-mail *</div>
    <div class="field" style="top:260px">Phone Number *</div>
    <div class="field" style="top:320px;border:none">Message</div>
    <span class="submit">Submit</span>
  </div>
  <div class="map" role="img" aria-label="Street map showing the office location">
    <svg class="abs" style="left:258px;top:170px" width="24" height="34" viewBox="0 0 24 34"><path d="M12 0a12 12 0 0 1 12 12c0 9-12 22-12 22S0 21 0 12A12 12 0 0 1 12 0z" fill="#d7262e"/><circle cx="12" cy="12" r="4.5" fill="#fff"/></svg>
  </div>
</section>

<footer class="site-footer">
  <div class="foot-brand">RIDGELINE</div>
  <div class="foot-brand-sub">HAUL CARRIERS</div>

  <div class="foot-col" style="left:436px;width:300px">
    <h4>CONTACT US</h4>
    <ul>
      <li><svg width="14" height="18" viewBox="0 0 24 34"><path d="M12 0a12 12 0 0 1 12 12c0 9-12 22-12 22S0 21 0 12A12 12 0 0 1 12 0z" fill="#cfd1d5"/></svg>2140 Cedar Bend Road, Unit 12, Box 418, Harlow, Ontario K0A 1B9</li>
      <li><svg width="14" height="14" viewBox="0 0 24 24"><path d="M6.6 10.8a15.1 15.1 0 0 0 6.6 6.6l2.2-2.2a1 1 0 0 1 1-.25 11.4 11.4 0 0 0 3.6.57 1 1 0 0 1 1 1V20a1 1 0 0 1-1 1A17 17 0 0 1 3 4a1 1 0 0 1 1-1h3.5a1 1 0 0 1 1 1c0 1.25.2 2.45.57 3.57a1 1 0 0 1-.25 1z" fill="#cfd1d5"/></svg>1-800-555-0148</li>
      <li><svg width="16" height="12" viewBox="0 0 24 18"><rect x="1" y="1" width="22" height="16" fill="none" stroke="#cfd1d5" stroke-width="2"/><path d="M1 1l11 9 11-9" fill="none" stroke="#cfd1d5" stroke-width="2"/></svg>info@ridgelinehaul.example</li>
    </ul>
  </div>

  <div class="foot-col" style="left:780px">
    <h4>RESOURCES</h4>
    <ul>
      <li><span class="bullet"></span>Home</li>
      <li><span class="bullet"></span>About us</li>
      <li><span class="bullet"></span>Services</li>
      <li><span class="bullet"></span>Jobs</li>
      <li><span class="bullet"></span>Contact Us</li>
    </ul>
  </div>

  <div class="foot-col" style="left:980px">
    <h4>FOLLOW US</h4>
    <ul>
      <li style="align-items:center"><span class="ring"></span>Community</li>
      <li style="align-items:center"><span class="ring"></span>Updates</li>
      <li style="align-items:center"><span class="ring"></span>Gallery</li>
    </ul>
  </div>

  <div class="foot-bottom">© Copyright 2020 . All Rights Reserved. Terms and Conditions | Privacy Policy</div>
</footer>

</body>
</html>
```